BrivoTerna. Lantern of the Steady Harvest. Business card

Professional business card for BrivoTerna (Lantern of the Steady Harvest)
My rationale: Strategy-> Execution-> Results-> Value that lead to the BrivoTerna name: We put the Lantern of the Steady Harvest.
We deliver value to our customers helping them at defining a good strategy (cyan arrow). 90% of well formulated strategies fail due to poor execution so we also consider strategical execution very important (green arrow). Due to the execution we obtain the results (blue arrow). Finally, the results provide feedback to redefine strategy, and the new strategy has to be executed and new results obtained providing new feedback and on and on. It's like a wheel that finally, must create corporate value: value for shareholders, staholders, employees, providers...-

Target Market(s)

CEOs and steering comitees , invewrnent funds

Industry/Entity Type

Business Consultant

Contact Information for Business Card

Teodoro Vinsquel
CEO & Founder
teodoro.vinsquel@brivoterna-example.com
Mobile: +34 655.803.912
www.brivoterna-example.com

Colors

Designer to choose colors to be used in the design.

Requirements
Nice to have
• Nice to hace the words: Strategy, execution, results
• Nice to vave the claim: Lantern of the Steady Harvest
• The three colors should be shown:
• cyan for STRATEGY
• green for EXECUTION
• blue for RESULTS
Should not have
• Complete black background

```html
<!DOCTYPE html>
<html lang="en">
<head>
<meta charset="utf-8">
<title>BrivoTerna — Business Card</title>
<link rel="stylesheet" href="https://fonts.googleapis.com/css2?family=Open+Sans:wght@400;600;700;800&display=swap">
<style>
  :root {
    --brand-blue: #0a3595;
    --brand-green: #8cc63f;
    --brand-cyan: #29b6e8;
    --paper: #ffffff;
    --backdrop: #e4e1dd;
    --ink-dark: #1f2a44;
  }
  * { box-sizing: border-box; margin: 0; padding: 0; }
  html, body {
    width: 1200px; height: 997px; overflow: hidden;
    background: var(--backdrop);
    font-family: "Open Sans", Arial, sans-serif;
  }
  .sheet {
    width: 1200px; height: 997px;
    display: flex; flex-direction: column; align-items: center; justify-content: center;
    gap: 60px;
  }
  .card {
    position: relative; width: 700px; height: 400px; overflow: hidden;
    box-shadow: 0 6px 18px rgba(0,0,0,0.12);
  }

  /* Front */
  .card--front { background: var(--paper); }
  .wordmark {
    position: absolute; left: 70px; top: 120px;
    display: flex; align-items: center; gap: 14px;
    font-weight: 800; font-size: 50px; letter-spacing: -1px;
    color: var(--brand-blue);
  }
  .wordmark__dot {
    width: 18px; height: 18px; border-radius: 50%;
    background: var(--brand-cyan);
  }
  .name-band {
    position: absolute; left: 0; top: 232px; width: 420px; height: 74px;
  }
  .name-band__shape { position: absolute; inset: 0; }
  .name-band__text { position: absolute; left: 70px; top: 8px; }
  .person-name {
    font-weight: 700; font-size: 28px; color: var(--brand-blue); line-height: 1.15;
  }
  .person-role {
    font-weight: 400; font-size: 19px; color: var(--ink-dark);
  }
  .contact-panel { position: absolute; inset: 0; }
  .contact-list {
    position: absolute; left: 418px; top: 168px; list-style: none;
    color: var(--paper); font-size: 14px; line-height: 1.9;
  }
  .contact-list li { display: flex; align-items: center; gap: 9px; }
  .contact-list svg { width: 14px; height: 14px; flex: none; }

  /* Back */
  .card--back { background: var(--brand-blue); }
  .back-wordmark {
    position: absolute; left: 0; right: 0; top: 140px; text-align: center;
    font-weight: 800; font-size: 92px; letter-spacing: -2px; color: var(--paper);
  }
  .tagline-tab {
    position: absolute; right: 120px; bottom: 0; width: 300px; height: 46px;
    background: var(--paper); border-radius: 18px 18px 0 0;
    display: flex; align-items: center; justify-content: center;
    font-weight: 700; font-size: 16px; color: var(--brand-blue);
  }
</style>
</head>
<body>
<main class="sheet">

  <section class="card card--front" aria-label="Business card front">
    <svg class="contact-panel" width="700" height="400" viewBox="0 0 700 400" aria-hidden="true">
      <polygon points="390,130 700,130 700,400 330,400" fill="var(--brand-blue)"/>
    </svg>

    <div class="wordmark"><span class="wordmark__dot"></span>BrivoTerna</div>

    <div class="name-band">
      <svg class="name-band__shape" width="420" height="74" viewBox="0 0 420 74" aria-hidden="true">
        <polygon points="0,0 400,0 420,37 400,74 0,74" fill="var(--brand-green)"/>
      </svg>
      <div class="name-band__text">
        <p class="person-name">Teodoro Vinsquel</p>
        <p class="person-role">CEO &amp; Founder</p>
      </div>
    </div>

    <ul class="contact-list">
      <li>
        <svg viewBox="0 0 14 14" aria-hidden="true"><rect x="3.5" y="1" width="7" height="12" rx="1.5" fill="none" stroke="currentColor" stroke-width="1.4"/><circle cx="7" cy="11" r="0.8" fill="currentColor"/></svg>
        +34 655.803.912
      </li>
      <li>
        <svg viewBox="0 0 14 14" aria-hidden="true"><rect x="1" y="3" width="12" height="8" rx="1" fill="none" stroke="currentColor" stroke-width="1.4"/><polyline points="1,3 7,8 13,3" fill="none" stroke="currentColor" stroke-width="1.4"/></svg>
        teodoro.vinsquel@brivoterna-example.com
      </li>
      <li>
        <svg viewBox="0 0 14 14" aria-hidden="true"><circle cx="7" cy="7" r="5.5" fill="none" stroke="currentColor" stroke-width="1.3"/><ellipse cx="7" cy="7" rx="2.3" ry="5.5" fill="none" stroke="currentColor" stroke-width="1.1"/><line x1="1.5" y1="7" x2="12.5" y2="7" stroke="currentColor" stroke-width="1.1"/></svg>
        www.brivoterna-example.com
      </li>
    </ul>
  </section>

  <section class="card card--back" aria-label="Business card back">
    <p class="back-wordmark">BrivoTerna</p>
    <p class="tagline-tab">Results - Execution - Strategy</p>
  </section>

</main>
</body>
</html>
```